Business Card Design Project - del varosi group

dear Sirs

we need business card design for our group ( DEL Varosi Group ) , i have got the Logo design of our group from pixel harbor in previous , so all need details relating to our group i think available with you, as well as the the chosen logo design

we hope to provide us with business card logo that to be appropaite and satisfactory to us .

thanks

note : logo design of our group is attached .
Updates

Reason: please extend the deadline of my project for additional 15 days because i didn't received appropriate design for our gruop yet . kindly beaware that i have received 77 design till now , supossed to send me 200-250 design at least . thanks

Target Market(s)

contents

name : Kerem EL Nadiri

position : Operation Manager

Industry/Entity Type

Business

Requirements
Must have

• person name

group logo
Nice to have
• logo color matching with back background

```html
<!DOCTYPE html>
<html lang="en">
<head>
<meta charset="utf-8">
<title>DEL Varosi Group – Business Card</title>
<link rel="stylesheet" href="https://fonts.googleapis.com/css2?family=Questrial&family=Open+Sans:wght@400;600&display=swap">
<style>
  :root {
    --page-bg: #efe8d4;
    --card-white: #ffffff;
    --navy: #183f7a;
    --navy-deep: #0f2d5c;
    --gold: #c49a3a;
    --gold-light: #dcbb6c;
    --ink: #2b2b2b;
    --title-white: #e8eef8;
  }
  * { box-sizing: border-box; margin: 0; padding: 0; }
  html, body { width: 1200px; height: 951px; overflow: hidden; }
  body {
    background: var(--page-bg);
    font-family: "Open Sans", Arial, sans-serif;
    position: relative;
  }
  .card {
    position: absolute;
    width: 560px;
    height: 320px;
    border-radius: 22px;
    background: var(--card-white);
    overflow: hidden;
    box-shadow: 0 6px 18px rgba(80, 60, 20, 0.18);
  }
  .card-front { left: 90px; top: 110px; }
  .card-back  { left: 550px; top: 500px; }

  .wordmark {
    font-family: "Questrial", Arial, sans-serif;
    color: var(--navy);
    display: flex;
    align-items: center;
    gap: 14px;
    white-space: nowrap;
  }
  .wordmark-square {
    display: inline-block;
    background: var(--navy);
  }
  .card-front .wordmark {
    position: absolute;
    left: 70px; top: 102px;
    font-size: 46px;
    letter-spacing: 1px;
  }
  .card-front .wordmark-square { width: 30px; height: 30px; }
  .card-front .website {
    position: absolute;
    left: 160px; top: 212px;
    font-size: 17px;
    letter-spacing: 1.5px;
    color: var(--gold);
  }

  .back-art { position: absolute; inset: 0; }
  .card-back .wordmark {
    position: absolute;
    left: 32px; top: 30px;
    font-size: 25px;
  }
  .card-back .wordmark-square { width: 16px; height: 16px; }

  .contact-list {
    position: absolute;
    left: 32px; top: 104px;
    list-style: none;
    font-size: 14px;
    line-height: 1.3;
    color: var(--ink);
  }
  .contact-list li {
    display: flex;
    align-items: flex-start;
    gap: 8px;
    margin-bottom: 3px;
  }
  .contact-list svg { width: 13px; height: 13px; flex: none; margin-top: 3px; }
  .contact-list .address { margin-bottom: 8px; }
  .accent { color: var(--gold); }

  .person {
    position: absolute;
    left: 372px; top: 150px;
  }
  .person-name {
    font-size: 19px;
    color: var(--gold-light);
    font-weight: 400;
    letter-spacing: 0.3px;
  }
  .person-title {
    margin-top: 4px;
    font-size: 14px;
    color: var(--title-white);
  }
</style>
</head>
<body>

  <section class="card card-front" aria-label="Business card front">
    <div class="wordmark"><span class="wordmark-square"></span>DEL Varosi Group</div>
    <p class="website">www.delvarosigroup.com</p>
  </section>

  <section class="card card-back" aria-label="Business card back">
    <svg class="back-art" viewBox="0 0 560 320" preserveAspectRatio="none" aria-hidden="true">
      <path d="M335 0 C 300 90, 300 220, 250 320 L 560 320 L 560 0 Z" fill="var(--gold)"/>
      <path d="M350 0 C 318 90, 318 220, 272 320 L 560 320 L 560 0 Z" fill="var(--navy)"/>
      <path d="M0 320 C 120 305, 220 290, 300 240 C 290 270, 275 300, 262 320 Z" fill="var(--gold)" opacity="0.85"/>
    </svg>

    <div class="wordmark"><span class="wordmark-square"></span>DEL Varosi Group</div>

    <ul class="contact-list">
      <li class="address">
        <svg viewBox="0 0 12 12"><path d="M6 1 L11 6 H9.5 V11 H7 V8 H5 V11 H2.5 V6 H1 Z" fill="var(--gold)"/></svg>
        <span>4100 Alder Crest Bd.<br>Suite 208-140<br>Marlow, TX 78090</span>
      </li>
      <li>
        <svg viewBox="0 0 12 12"><path d="M3 1 L5 3.5 L4 5 C5 7 6 8 7.5 8.5 L9 7.5 L11 9.5 L9.5 11 C5 10.5 1.5 7 1 2.5 Z" fill="var(--gold)"/></svg>
        <span>512-555-0142</span>
      </li>
      <li>
        <svg viewBox="0 0 12 12"><rect x="1" y="5" width="10" height="5" rx="1" fill="var(--gold)"/><rect x="3" y="2" width="6" height="3" fill="var(--gold)"/></svg>
        <span>512-555-0143</span>
      </li>
      <li>
        <svg viewBox="0 0 12 12"><rect x="1" y="2.5" width="10" height="7" rx="1" fill="var(--gold)"/><path d="M1.5 3 L6 6.5 L10.5 3" stroke="#fff" fill="none"/></svg>
        <span>info@<span class="accent">delvarosigroup</span>.com</span>
      </li>
      <li>
        <svg viewBox="0 0 12 12"><circle cx="6" cy="6" r="5" fill="var(--gold)"/></svg>
        <span>www.<span class="accent">delvarosigroup</span>.com</span>
      </li>
    </ul>

    <div class="person">
      <p class="person-name">Kerem EL Nadiri</p>
      <p class="person-title">Operation Manager</p>
    </div>
  </section>

</body>
</html>
```